Heron Loan Partners Business Card

We need a business card design for our mortgage servicing company. In addition to servicing the loans of homeowners, we help homeowners with purchasing their homes and any mortgage refinancing. We would like to see designs that use the colors in the logo attached below (gold-ish yellow and navy blue), and any other design you deem fit! The design should communicate a simpler life with smart mortgages provided by Heron.

```html
<!DOCTYPE html>
<html lang="en">
<head>
<meta charset="utf-8">
<title>Heron Loan Partners Business Card</title>
<link rel="stylesheet" href="https://fonts.googleapis.com/css2?family=Montserrat:wght@400;500;700&display=swap">
<style>
  :root {
    --navy: #25205e;
    --gold: #e0b43c;
    --ink: #1b1b1b;
    --paper: #ffffff;
    --backdrop: #5a5a5a;
  }
  * { margin: 0; padding: 0; box-sizing: border-box; }
  html, body { width: 1200px; height: 900px; overflow: hidden; }
  body {
    background: var(--backdrop);
    font-family: "Montserrat", sans-serif;
    color: var(--ink);
    position: relative;
  }
  .card {
    position: absolute;
    left: 250px;
    width: 700px;
    height: 400px;
    background: var(--paper);
    overflow: hidden;
    box-shadow: 0 10px 30px rgba(0,0,0,0.35);
  }
  .card-front { top: 30px; }
  .card-back { top: 470px; }

  .wordmark {
    display: flex;
    align-items: center;
    gap: 12px;
    color: var(--gold);
    font-weight: 700;
    white-space: nowrap;
  }
  .wordmark-dot {
    background: var(--navy);
    border-radius: 50%;
    flex: none;
  }
  .card-front .wordmark {
    position: absolute;
    left: 50%; top: 50%;
    transform: translate(-50%, -50%);
    font-size: 44px;
  }
  .card-front .wordmark-dot { width: 26px; height: 26px; }

  .card-back .wordmark {
    position: absolute;
    left: 300px; top: 62px;
    font-size: 26px;
  }
  .card-back .wordmark-dot { width: 16px; height: 16px; }

  .identity {
    position: absolute;
    left: 56px; top: 150px;
    padding-left: 20px;
    border-left: 10px solid var(--gold);
  }
  .identity-name {
    font-weight: 700;
    font-size: 20px;
    letter-spacing: 0.5px;
    color: var(--navy);
  }
  .identity-name .surname { color: var(--gold); }
  .identity-role { font-size: 17px; margin-top: 2px; }

  .contacts {
    position: absolute;
    left: 76px; top: 222px;
    list-style: none;
  }
  .contact {
    display: flex;
    align-items: center;
    gap: 12px;
    font-size: 17px;
    margin-bottom: 9px;
  }
  .contact-icon { width: 18px; height: 18px; flex: none; }

  .address {
    position: absolute;
    right: 40px; top: 128px;
    font-size: 16px;
    line-height: 1.4;
    text-align: left;
  }
  .wave { position: absolute; left: 0; top: 0; }
</style>
</head>
<body>

<section class="card card-front">
  <div class="wordmark"><span class="wordmark-dot"></span>Heron Loan Partners</div>
</section>

<section class="card card-back">
  <svg class="wave" width="700" height="400" viewBox="0 0 700 400" aria-hidden="true">
    <path d="M0,400 L0,398 C300,397 460,315 570,265 C630,238 675,225 700,221 L700,400 Z" fill="var(--navy)"/>
    <path d="M0,388 C300,385 450,300 560,250 C620,222 670,208 700,203" fill="none" stroke="var(--gold)" stroke-width="5"/>
  </svg>

  <div class="wordmark"><span class="wordmark-dot"></span>Heron Loan Partners</div>

  <div class="identity">
    <p class="identity-name">DANA <span class="surname">WHITLOCK</span></p>
    <p class="identity-role">Owner</p>
  </div>

  <p class="address">2480 Alder Grove Ave, Ste 210<br>Fairview, TX 75069</p>

  <ul class="contacts">
    <li class="contact">
      <svg class="contact-icon" viewBox="0 0 20 20" aria-hidden="true"><path d="M5 2l3 4-2 2c1 2 3 4 6 6l2-2 4 3-2 3C9 18 2 11 2 4z" fill="var(--gold)"/></svg>
      555.201.4830
    </li>
    <li class="contact">
      <svg class="contact-icon" viewBox="0 0 20 20" aria-hidden="true"><rect x="2" y="4" width="16" height="12" fill="var(--gold)"/><path d="M2 4l8 7 8-7" fill="none" stroke="#fff" stroke-width="1.5"/></svg>
      info@heronloanpartners.com
    </li>
    <li class="contact">
      <svg class="contact-icon" viewBox="0 0 20 20" aria-hidden="true"><circle cx="10" cy="10" r="8" fill="var(--gold)"/><path d="M2 10h16M10 2c-4 5-4 11 0 16M10 2c4 5 4 11 0 16" fill="none" stroke="#fff" stroke-width="1.2"/></svg>
      www.heronloanpartners.com
    </li>
  </ul>
</section>

</body>
</html>
```